Medical Learning Web Design Project

The web site will be a site for medical students. It is aimed at providing a collaborative place for students to study, learn, question each other and challenge each other with learning. The site needs to have a section on the page that is for the content and this needs to be relatively clean and clinical. The surrounding elements will be informative (for the statistics, challenge etc). There will also be a slide-out screen that allows for the social/friend elements of the site.

The colour scheme needs to be clean and clinical where appropriate, but also engaging and exciting for the social/competitive elements.
Updates

Just for clarity: The site isn't expected to be 'coded' ... it is just the layered PSD files that I need.

Also, with regards to the navigation buttons ... they will never ALL be present at the same time so don't feel the need to design all on one page, but creativity around allowing few or many on a page will be an advantage ...

Thanks

Hi,

Please note that the image uploaded has been done as a wireframe by the developers. I am looking for a more creative and engaging way of presenting that content ...

Thanks

Hi all

Thank you all for the designs so far ...!

Please have a look at the new uploaded file, I am also looking not just for a 'templated home page' but also some different layouts that are represented in these wireframes. If the various layouts represented can be condensed down into 1 or 2 page templates with appropriate colour schemes to capture the type of content on the page (as already mentioned ... social .. competitive ... learning), then that will help me live the concepts better too! The friends tab for instance I have envisaged as a slider covering the screen and then sliding back when complete ... but let me see what creativity you can give to this ...!

Many thanks

Reason: Just allowing for final tweaks ...

Target Market(s)

Medical Students

Industry/Entity Type

Medical

Requirements
Must have
• - Not cluttered appearance
- Dynamic navigation (ie. site will be developed to only show relevant navigation buttons on each page ...)
- Navigation buttons (need to be individual buttons) will be: 'Home', 'Take the tour', 'What your peers say', 'Subscriptions', 'Free Signup', 'Contact us', 'Moderation', 'Statistics', 'Competition', 'Answer Questions', 'Post Questions', 'My profile', 'Friends'
- Please also ensure it is engaging for social elements and competitive elements (perhaps slightly different design for pages focussed on each element)
- Please also ensure that there is a masculine design and feminine design that has continuity for the site but depending on gender the design can be tailored to be more appealing (that means perhaps male social design, male competitive design, female social design, female competitive design ... without loosing continuity through the site).
- Photoshop PSD format
- Pixel perfect at least 1000 pixels wide (but the design needs to allow for various monitor sizes (only desktop or laptops ... not tablets or smart phones)

```html
<!DOCTYPE html>
<html lang="en">
<head>
<meta charset="utf-8">
<title>Medora – The Medical Peer Review</title>
<link href="https://fonts.googleapis.com/css2?family=Source+Sans+3:ital,wght@0,400;0,600;0,700;1,600&display=swap" rel="stylesheet">
<style>
:root{
  --topbar:#2f4a66;
  --header:#4c78a2;
  --page:#efefef;
  --white:#ffffff;
  --nav-bg:#ededed;
  --ticker-bg:#f5f5f5;
  --blue-text:#3d6a96;
  --nav-text:#5b7fa3;
  --orange:#f08a14;
  --orange-light:#f8b85a;
  --orange-dark:#e08c25;
  --dark:#2b2b2b;
  --line:#c8c8c8;
  --green:#74a120;
  --grey-text:#555;
}
*{box-sizing:border-box;margin:0;padding:0}
html,body{width:1200px;height:976px;overflow:hidden}
body{font-family:"Source Sans 3",sans-serif;background:var(--page);position:relative;color:var(--dark)}
.abs{position:absolute}
.topbar{left:0;top:0;width:1200px;height:26px;background:var(--topbar)}
.topbar .web{position:absolute;right:182px;top:6px;color:#fff;font-size:11px;font-weight:700}
.topbar .social{position:absolute;right:10px;top:5px;display:flex;gap:9px}
.topbar .social span{width:13px;height:13px;border-radius:2px;display:block}
.header{left:0;top:26px;width:1200px;height:379px;background:var(--header)}
.logo{left:192px;top:36px;color:#fff}
.logo .name{font-size:40px;font-weight:400;letter-spacing:1px;line-height:1}
.logo .tag{font-size:12.5px;font-weight:700;margin-top:6px;margin-left:0}
.quote{left:330px;top:44px;width:428px;color:#fff;font-style:italic;font-weight:600;font-size:12.5px;line-height:15px;text-align:right}
.quote .ask{display:block;text-align:center;font-size:14px;margin-top:5px;margin-left:30px;font-weight:600}
.login input{position:absolute;width:93px;height:25px;border:1px solid #d8d8d8;background:#f6f6f6;font:10px "Source Sans 3",sans-serif;color:#555;padding-left:8px}
.keep{left:818px;top:78px;color:#fff;font-size:10px;font-weight:600;display:flex;align-items:center;gap:5px}
.keep i{width:10px;height:10px;background:#e5e5e5;display:block}
.forgot{left:832px;top:96px;color:#fff;font-size:10px;font-weight:600}
.loginbtn{left:954px;top:84px;width:59px;height:22px;border-radius:11px;background:linear-gradient(#ffd35a,#f6ab18);color:#2b2b2b;font-size:10px;font-weight:700;text-align:center;line-height:22px}
.rule{left:187px;top:132px;width:826px;height:1px;background:#7096bb}
.main{left:187px;top:141px;width:826px;height:835px;background:var(--white)}
.nav{left:187px;top:141px;width:826px;height:50px;background:var(--nav-bg);display:flex}
.nav .item{height:50px;border-right:1px solid #dcdcdc;display:flex;flex-direction:column;align-items:center;justify-content:flex-end;padding-bottom:7px;color:var(--nav-text);font-size:11.5px;gap:5px}
.nav .item svg{width:16px;height:16px}
.nav .home{color:var(--orange)}
.nav .more{background:#fff;border:1px solid #ccc;border-bottom:none;margin-top:6px;height:44px;border-radius:3px 3px 0 0;font-weight:600}
.ticker{left:187px;top:191px;width:826px;height:37px;background:var(--ticker-bg)}
.ticker p{position:absolute;left:15px;top:11px;font-size:12px;font-weight:600;color:var(--blue-text)}
.ticker p u{text-decoration:underline}
.likebtn{left:754px;top:203px;width:40px;height:15px;border:1px solid #9aa9c0;border-radius:2px;background:#eef1f6;font-size:9px;color:#3b5998;display:flex;align-items:center;gap:3px;padding-left:3px}
.likebtn i{width:9px;height:9px;background:#3b5998;display:block}
.count{left:801px;top:203px;width:29px;height:15px;border:1px solid #999;background:#fff;font-size:9px;text-align:center;line-height:13px}
.dropdown{left:850px;top:187px;width:147px;height:130px;background:#fff;border:1px solid #ccc;border-top:none;border-radius:0 0 3px 3px;padding:8px 8px 0 8px;box-shadow:0 2px 4px rgba(0,0,0,.15)}
.dropdown li{list-style:none;font-size:11.5px;font-weight:600;color:var(--blue-text);height:17px;border-bottom:1px dotted #d0d8e2;display:flex;align-items:center;gap:8px}
.dropdown li:last-child{border:none}
.dropdown li b{font-size:10px;color:#3d6a96}
.slider{left:200px;top:245px;width:800px;height:352px;border:1px solid #ddd;background:#fff;padding:2px}
.slide{width:794px;height:346px;background:linear-gradient(180deg,var(--orange-light),var(--orange-dark))}
.slide-title{left:250px;top:283px;font-size:24px;color:#222;display:flex;align-items:baseline;gap:8px}
.slide-title .brand{font-size:26px;text-decoration:underline;text-decoration-thickness:1px;text-underline-offset:3px}
.slide-title .rest{font-size:20px}
.features{left:248px;top:334px;list-style:none}
.features li{font-size:15.5px;color:#2a2a2a;height:30.3px;display:flex;gap:10px;align-items:center}
.features li b{font-size:13px;font-weight:700}
.tile{width:167px;height:125px;border:3px solid #fff;border-radius:3px;box-shadow:0 1px 3px rgba(0,0,0,.2)}
.arrow{width:36px;height:36px;border-radius:50%;background:#f4d8aa;display:flex;align-items:center;justify-content:center}
.dots{left:560px;top:570px;width:81px;height:27px;border-radius:10px 10px 0 0;background:#f0a545;display:flex;justify-content:center;align-items:center;gap:7px}
.dots i{width:10px;height:10px;border-radius:50%;background:#fff;display:block}
.dots i.on{box-shadow:inset 0 0 0 2px #fff;background:#4c78a2}
.panel{top:632px;width:244px;height:236px;border:1px solid #c6c6c6;background:#fff}
.panel h2{height:26px;border-bottom:1px solid #c6c6c6;font-size:19px;font-weight:400;padding-left:12px;line-height:28px}
.panel .foot{position:absolute;left:0;bottom:0;width:100%;height:18px;border-top:1px solid #c6c6c6;background:#f4f4f4;font-size:9.5px;padding:0 10px;display:flex;justify-content:space-between;align-items:center}
.video{left:10px;top:44px;width:219px;height:147px;background:#000;border-radius:3px}
.post{margin:0 9px;padding:7px 0 6px;border-bottom:1px solid #ccc;font-family:Arial,sans-serif;font-size:9.5px;line-height:15px;color:#333}
.post .date{font-weight:700;font-size:8.5px}
.post:last-of-type{border:none}
.fb-top{height:44px;border-bottom:1px solid #c6c6c6;display:flex;align-items:center;padding:0 10px;gap:26px}
.fb-brand{border:1px solid #9aa9c0;width:68px;height:30px;color:#3d6a96;font-size:19px;text-align:center;line-height:28px}
.fb-stats{font-size:13px;color:#3d6a96;font-weight:600;line-height:14px}
.fb-stats small{display:block;font-size:8.5px;font-weight:400;color:#333}
.friends{display:grid;grid-template-columns:repeat(4,47px);column-gap:9px;row-gap:8px;padding:7px 0 0 12px}
.friend{text-align:center;font-size:8.5px;color:#666;font-family:Arial,sans-serif}
.friend .pic{width:47px;height:47px;margin-bottom:3px}
.footer-rule{left:187px;top:918px;width:826px;height:1px;background:#e2e2e2;box-shadow:0 -2px 4px rgba(0,0,0,.06)}
.footer-links{left:187px;top:936px;width:826px;text-align:center;font-size:10.5px;color:var(--blue-text);font-weight:600}
.footer-links span{margin:0 7px;font-weight:400}
.copy{left:187px;top:953px;width:826px;text-align:center;font-size:10.5px;color:var(--blue-text);font-weight:600}
</style>
</head>
<body>
<div class="abs topbar">
  <div class="web">Medora on the web:</div>
  <div class="social">
    <span style="background:#3b5998"></span><span style="background:#e23a2f"></span><span style="background:#4ab3e8"></span><span style="background:#2fa6d8"></span><span style="background:#6a8a3a"></span><span style="background:#cc2127"></span>
  </div>
</div>
<div class="abs header"></div>
<div class="abs logo"><div class="name">medora</div><div class="tag">The Medical Peer Review</div></div>
<div class="abs quote">“Medora keeps me ahead of the game, constantly testing my knowledge...”<br>Sam, doctor in training, Northfield University<span class="ask">How will your stats compare</span></div>
<div class="login">
  <input style="left:818px;top:45px" value="Username" readonly>
  <input style="left:920px;top:45px" value="Password" readonly>
</div>
<div class="abs keep"><i></i>Keep me Signed in</div>
<div class="abs forgot">Forgot your password</div>
<div class="abs loginbtn">LOGIN</div>
<div class="abs rule"></div>

<div class="abs main"></div>
<nav class="abs nav">
  <div class="item home" style="width:96px"><svg viewBox="0 0 16 16"><path d="M8 2 1 8h2v6h4v-4h2v4h4V8h2z" fill="#f08a14"/></svg>Home</div>
  <div class="item" style="width:118px"><svg viewBox="0 0 16 16"><rect x="2" y="5" width="12" height="9" fill="none" stroke="#4c78a2" stroke-width="2"/><path d="M5 1l3 4 3-4" fill="none" stroke="#4c78a2" stroke-width="1.5"/></svg>Take the tour</div>
  <div class="item" style="width:155px"><svg viewBox="0 0 16 16"><circle cx="5.5" cy="5" r="2.5" fill="#4c78a2"/><circle cx="11" cy="4.5" r="2.5" fill="#4c78a2"/><path d="M1 14c0-4 2-6 4.5-6S10 10 10 14zM9 9c1-1 1.5-1.5 2-1.5 2.5 0 4 2 4 6h-4" fill="#4c78a2"/></svg>What your peers say</div>
  <div class="item" style="width:147px"><svg viewBox="0 0 16 16"><path d="M8 1l2.1 4.6 5 .5-3.8 3.3 1.1 4.9L8 11.8 3.6 14.3l1.1-4.9L.9 6.1l5-.5z" fill="#4c78a2"/></svg>Subscription Plans</div>
  <div class="item" style="width:114px"><svg viewBox="0 0 16 16"><rect x="3" y="3" width="10" height="7" fill="none" stroke="#4c78a2" stroke-width="1.6"/><rect x="1" y="11" width="14" height="2" fill="#4c78a2"/></svg>Free Signup</div>
  <div class="item" style="width:122px"><svg viewBox="0 0 16 16"><rect x="5" y="1" width="6" height="14" rx="1" fill="none" stroke="#4c78a2" stroke-width="1.6"/><circle cx="8" cy="12.5" r=".9" fill="#4c78a2"/></svg>Contact Us</div>
  <div class="item more" style="width:57px"><svg viewBox="0 0 16 16"><circle cx="8" cy="8" r="7" fill="#3d6a96"/><path d="M8 4v8M4 8h8" stroke="#fff" stroke-width="2"/></svg>More</div>
</nav>
<div class="abs ticker"><p>about 2 days ago: Medora is now on Friendbook. Follow us <u>here.</u></p></div>
<div class="abs likebtn"><i></i>Like</div>
<div class="abs count">4K</div>

<div class="abs slider"><div class="slide"></div></div>
<div class="abs slide-title"><span class="brand">medora</span><span class="rest">- The Medical Peer Review</span></div>
<ul class="abs features">
  <li><b>»</b>Test your medical knowledge</li>
  <li><b>»</b>Answer a vast array of medical questions</li>
  <li><b>»</b>Earn trophies as your knowledge increases</li>
  <li><b>»</b>Rate questions from peers</li>
  <li><b>»</b>Ask your own questions</li>
  <li><b>»</b>Link to your friend and check their progress</li>
  <li><b>»</b>29.903 Questions answered!</li>
</ul>
<div class="abs tile" style="left:603px;top:287px;background:linear-gradient(135deg,#f7f7f7,#e3c28c)" role="img" aria-label="Illustration of a question mark figure with a medical kit"></div>
<div class="abs tile" style="left:780px;top:287px;background:linear-gradient(135deg,#e8e8e8,#a9a9a9)" role="img" aria-label="Photo of a stethoscope resting on an open book"></div>
<div class="abs tile" style="left:603px;top:422px;background:linear-gradient(180deg,#f4f4f4,#5c84a8)" role="img" aria-label="Illustration of medical icons linked in a network"></div>
<div class="abs tile" style="left:780px;top:422px;background:linear-gradient(180deg,#f4f4f4,#c9d6de)" role="img" aria-label="Illustration of medical staff connected in a circle"></div>
<div class="abs arrow" style="left:205px;top:403px"><svg width="14" height="16" viewBox="0 0 14 16"><path d="M10 2 4 8l6 6" fill="none" stroke="#333" stroke-width="3"/></svg></div>
<div class="abs arrow" style="left:960px;top:403px"><svg width="14" height="16" viewBox="0 0 14 16"><path d="M4 2l6 6-6 6" fill="none" stroke="#222" stroke-width="3"/></svg></div>
<div class="abs dots"><i class="on"></i><i></i><i></i></div>

<ul class="abs dropdown">
  <li><b>»</b>Moderation</li><li><b>»</b>Statistics</li><li><b>»</b>Competition</li><li><b>»</b>Answer Questions</li><li><b>»</b>Post Questions</li><li><b>»</b>My profile</li><li><b>»</b>Friends</li>
</ul>

<section class="abs panel" style="left:201px">
  <h2 style="color:#3d6a96">How Medora Works</h2>
  <div class="abs video"><svg class="abs" style="left:92px;top:55px" width="38" height="38" viewBox="0 0 38 38"><circle cx="19" cy="19" r="17" fill="#444" stroke="#bbb" stroke-width="2"/><path d="M15 11l11 8-11 8z" fill="#ddd"/></svg></div>
  <div class="foot"><u style="color:#3d6a96">click to play video tour</u></div>
</section>
<section class="abs panel" style="left:479px">
  <h2 style="color:var(--green)">Medora <span style="font-size:12px;font-weight:600">-Medical Peer Review</span></h2>
  <div class="post">Lorem Ipsum is simply dummy text of the printing and typesetting industry.<div class="date">09/13/2012</div></div>
  <div class="post">Lorem Ipsum is simply dummy text of the printing and typesetting industry.<div class="date">09/12/2012</div></div>
  <div class="post">Lorem Ipsum is simply dummy text of the printing and typesetting industry.<div class="date">09/11/2012</div></div>
  <div class="foot"><span style="color:#33c1ee">chirper</span><span style="color:#333;font-weight:600">Join the Conversation</span></div>
</section>
<section class="abs panel" style="left:756px">
  <h2 style="color:#e08818">Medora on Friendbook:</h2>
  <div class="fb-top"><div class="fb-brand">medora</div><div class="likebtn" style="position:static;width:38px;height:18px">Like</div><div class="fb-stats">6,836<small>people likes Medora</small></div></div>
  <div class="friends">
    <div class="friend"><div class="pic" style="background:#a88a72" role="img" aria-label="Profile photo"></div>Lena</div>
    <div class="friend"><div class="pic" style="background:#8a7f88" role="img" aria-label="Profile photo"></div>Rosa</div>
    <div class="friend"><div class="pic" style="background:#b08866" role="img" aria-label="Profile photo"></div>Oscar</div>
    <div class="friend"><div class="pic" style="background:#9a6a52" role="img" aria-label="Profile photo"></div>Tessa</div>
    <div class="friend"><div class="pic" style="background:#8c6a4e" role="img" aria-label="Profile photo"></div>Nina</div>
    <div class="friend"><div class="pic" style="background:#c29a7a" role="img" aria-label="Profile photo"></div>Edith</div>
    <div class="friend"><div class="pic" style="background:#9a7050" role="img" aria-label="Profile photo"></div>Robin</div>
    <div class="friend"><div class="pic" style="background:#6a6a6a" role="img" aria-label="Profile photo"></div>Poppy</div>
  </div>
  <div class="foot" style="justify-content:flex-start;gap:5px;color:#333"><i style="width:11px;height:11px;background:#3b5998;display:block"></i>Friendbook social plugin</div>
</section>

<div class="abs footer-rule"></div>
<div class="abs footer-links">Home<span>|</span>Take the tour<span>|</span>What your peers say<span>|</span>Subscription Plans<span>|</span>Free Signup<span>|</span>Contact Us</div>
<div class="abs copy">Copyright 2012 Medora Limited | All Rights Reserved</div>
</body>
</html>
```